Vantro cards

I am in the auto motive, transportation business I would like a business card that is Something cool, modern edgy, having to do with car culture. I offer towing service for high and exotic cars. I also provide towing for collisions and car accidents. I offer open and enclosed transport nationwide.

Target Market(s)

Car culture people high end auto collectors

Industry/Entity Type

Towing car carrier

Contact Information for Business Card

My company colors black yellow and silver

Font styles to use
Serif

```html
<!DOCTYPE html>
<html lang="en">
<head>
<meta charset="UTF-8">
<title>Vantro Business Cards</title>
<link rel="stylesheet" href="https://fonts.googleapis.com/css2?family=Poppins:wght@400;500;700&display=swap">
<style>
  :root {
    --backdrop: #1c1c1c;
    --card-black: #0c0c0c;
    --brand-yellow: #f5d547;
    --text-silver: #bdbdbd;
    --text-white: #f2f2f2;
    --divider: #4a4a4a;
    --silver-light: #e6e6e6;
  }
  * { margin: 0; padding: 0; box-sizing: border-box; }
  html, body { width: 1200px; height: 900px; overflow: hidden; }
  body {
    background: var(--backdrop);
    font-family: "Poppins", sans-serif;
    display: flex;
    flex-direction: column;
    align-items: center;
    justify-content: center;
    gap: 60px;
  }
  .card {
    width: 560px;
    height: 320px;
    border-radius: 22px;
    background: var(--card-black);
    box-shadow: 0 18px 40px rgba(0,0,0,0.55);
    position: relative;
    overflow: hidden;
  }
  .card-front { display: flex; align-items: center; padding: 0 36px; }
  .brand-block {
    width: 226px;
    display: flex;
    align-items: center;
    gap: 12px;
    flex-shrink: 0;
  }
  .brand-mark {
    width: 20px; height: 20px;
    background: var(--brand-yellow);
    border-radius: 3px;
    flex-shrink: 0;
  }
  .brand-name {
    font-weight: 700;
    font-size: 38px;
    letter-spacing: 1px;
    color: var(--text-white);
    line-height: 1;
    white-space: nowrap;
  }
  .divider {
    width: 1px;
    height: 180px;
    background: var(--divider);
    margin: 0 30px 0 10px;
    flex-shrink: 0;
  }
  .contact-block { color: var(--text-silver); }
  .person-name {
    font-weight: 700;
    font-size: 22px;
    color: var(--brand-yellow);
    letter-spacing: 0.5px;
    line-height: 1.1;
  }
  .person-title { font-size: 14px; margin-bottom: 16px; }
  .contact-list { list-style: none; font-size: 14px; line-height: 1.7; }
  .contact-list li { display: flex; align-items: center; gap: 10px; white-space: nowrap; }
  .contact-list svg { width: 14px; height: 14px; flex-shrink: 0; }
  .address { font-size: 14px; line-height: 1.4; margin-top: 16px; }
  .card-back { display: flex; align-items: center; justify-content: center; }
  .back-brand {
    font-weight: 700;
    font-size: 84px;
    letter-spacing: 3px;
    color: var(--silver-light);
  }
</style>
</head>
<body>
  <section class="card card-front">
    <div class="brand-block">
      <span class="brand-mark"></span>
      <span class="brand-name">VANTRO</span>
    </div>
    <div class="divider"></div>
    <div class="contact-block">
      <p class="person-name">DORIAN VALE</p>
      <p class="person-title">Managing Director</p>
      <ul class="contact-list">
        <li>
          <svg viewBox="0 0 24 24" aria-hidden="true"><path fill="var(--brand-yellow)" d="M6.6 10.8a15.1 15.1 0 0 0 6.6 6.6l2.2-2.2a1 1 0 0 1 1-.25 11.4 11.4 0 0 0 3.6.57 1 1 0 0 1 1 1V20a1 1 0 0 1-1 1A17 17 0 0 1 3 4a1 1 0 0 1 1-1h3.5a1 1 0 0 1 1 1c0 1.25.2 2.450.57 3.57a1 1 0 0 1-.25 1z"/></svg>
          055-310 842 617
        </li>
        <li>
          <svg viewBox="0 0 24 24" aria-hidden="true"><path fill="var(--brand-yellow)" d="M2 5h20v14H2z"/><path fill="none" stroke="var(--card-black)" stroke-width="2" d="M2 5l10 8 10-8"/></svg>
          hello@vantrotow.com
        </li>
        <li>
          <svg viewBox="0 0 24 24" aria-hidden="true"><circle cx="12" cy="12" r="10" fill="none" stroke="var(--brand-yellow)" stroke-width="2"/><path fill="none" stroke="var(--brand-yellow)" stroke-width="1.6" d="M2 12h20M12 2c3 3 3 17 0 20M12 2c-3 3-3 17 0 20"/></svg>
          www.vantrotow.com
        </li>
      </ul>
      <p class="address">88, Quarry Bend Lane<br>30917, Eastland</p>
    </div>
  </section>

  <section class="card card-back">
    <span class="back-brand">VANTRO</span>
  </section>
</body>
</html>
```